Heron Loan Partners Business Card

We need a business card design for our mortgage servicing company. In addition to servicing the loans of homeowners, we help homeowners with purchasing their homes and any mortgage refinancing. We would like to see designs that use the colors in the logo attached below (gold-ish yellow and navy blue), and any other design you deem fit! The design should communicate a simpler life with smart mortgages provided by Heron.

```html
<!DOCTYPE html>
<html lang="en">
<head>
<meta charset="utf-8">
<title>Heron Loan Partners Business Card</title>
<link rel="stylesheet" href="https://fonts.googleapis.com/css2?family=Montserrat:wght@400;500;700&display=swap">
<style>
  :root {
    --navy: #241f55;
    --navy-light: #5a5585;
    --gold: #d1a63a;
    --text-grey: #6b6b6b;
    --card-white: #f7f7f7;
    --backdrop: #e4e4e4;
  }
  * { margin: 0; padding: 0; box-sizing: border-box; }
  html, body {
    width: 1200px; height: 1200px; overflow: hidden;
    background: var(--backdrop);
    font-family: "Montserrat", sans-serif;
  }
  .stage {
    width: 1200px; height: 1200px;
    display: flex; flex-direction: column; align-items: center; justify-content: center;
    gap: 60px;
  }
  .card {
    width: 840px; height: 480px; border-radius: 28px; position: relative; overflow: hidden;
    box-shadow: 0 10px 24px rgba(0,0,0,0.18);
  }
  /* Back side */
  .card-back {
    background: linear-gradient(100deg, var(--navy-light) 0%, var(--navy) 65%, var(--navy) 100%);
  }
  .back-pattern {
    position: absolute; inset: 0;
    background: linear-gradient(100deg, rgba(255,255,255,0.10), rgba(255,255,255,0.04));
  }
  .back-brand {
    position: absolute; right: 90px; bottom: 110px;
    display: flex; align-items: center; gap: 12px;
    font-weight: 700; font-size: 34px; color: var(--gold);
  }
  .brand-dot {
    width: 20px; height: 20px; border-radius: 50%; background: var(--gold);
  }
  /* Front side */
  .card-front { background: var(--card-white); }
  .front-brand {
    position: absolute; top: 62px; left: 0; right: 0;
    display: flex; justify-content: center; align-items: center; gap: 16px;
    font-weight: 700; font-size: 52px; color: var(--gold);
  }
  .front-brand .brand-dot { width: 28px; height: 28px; background: var(--navy); }
  .person {
    position: absolute; top: 196px; left: 0; right: 0; text-align: center;
  }
  .person-name { font-weight: 700; font-size: 34px; color: var(--gold); letter-spacing: 0.5px; }
  .person-title { font-weight: 500; font-size: 20px; color: var(--text-grey); margin-top: 4px; }
  .divider {
    position: absolute; top: 292px; left: 110px; right: 80px;
    height: 2px; background: var(--navy);
  }
  .contacts {
    position: absolute; left: 110px; top: 314px; list-style: none;
  }
  .contacts li {
    display: flex; align-items: center; gap: 14px;
    font-size: 21px; color: var(--text-grey); line-height: 38px;
  }
  .contacts svg { width: 20px; height: 20px; flex: none; }
  .address {
    position: absolute; right: 80px; top: 314px; text-align: right;
    font-size: 21px; line-height: 30px; color: var(--text-grey); font-style: normal;
  }
</style>
</head>
<body>
<main class="stage">
  <section class="card card-back" aria-label="Card back">
    <div class="back-pattern" role="img" aria-label="Repeating faint brand pattern across the navy background"></div>
    <div class="back-brand"><span class="brand-dot"></span>Heron Loan Partners</div>
  </section>

  <section class="card card-front" aria-label="Card front">
    <div class="front-brand"><span class="brand-dot"></span>Heron Loan Partners</div>
    <div class="person">
      <p class="person-name">Dalton Rae</p>
      <p class="person-title">Founder &amp; Director</p>
    </div>
    <div class="divider"></div>
    <ul class="contacts">
      <li>
        <svg viewBox="0 0 20 20" aria-hidden="true"><path fill="#d1a63a" d="M5 2l3 3-2 2.5c1 2 2.5 3.5 4.5 4.5L13 10l3 3-2 3c-6 0-11-5-11-11z"/></svg>
        (888)-555-0142
      </li>
      <li>
        <svg viewBox="0 0 20 20" aria-hidden="true"><rect x="1" y="4" width="18" height="12" rx="1" fill="#d1a63a"/><path d="M1.5 4.5L10 11l8.5-6.5" stroke="#fff" stroke-width="1.5" fill="none"/></svg>
        info@heronloans.com
      </li>
      <li>
        <svg viewBox="0 0 20 20" aria-hidden="true"><circle cx="10" cy="10" r="9" fill="#d1a63a"/><path d="M1 10h18M10 1c-4 4-4 14 0 18M10 1c4 4 4 14 0 18" stroke="#fff" stroke-width="1.3" fill="none"/></svg>
        www.heronloans.com
      </li>
    </ul>
    <address class="address">218 Harbor Ave N,<br>Clearwater,<br>FL 33755</address>
  </section>
</main>
</body>
</html>
```